International business needs business cards

Our company, DRV Ventures Inc. is in the business of supplying a range construction products with particular emphasis on CEMENT. We have developed our own brand - TORVAN SUPPLIES - with which to infiltrate the market. We are launching our brand of cement (TORVAN Type IS Cement) into the Caribbean which is unlike anything this market has ever seen. A monopoly has existed here for the past 60-odd years and the market has now opened to allow the importation of other brands and consumers are anxious and ready for change/improvement. We are very excited to be launching and want to make a great first impression. We will be conducting workshops and seminars (from government level to the hardware store owners) and we want our business card to give us the strong, confident introduction that we need.

Target Market(s)

construction; builders; engineers; home owners

Industry/Entity Type

Construction

Contact Information for Business Card

Marisol Depree
CEO
cell # 1 555 4180736
Ground floor,Lindell Plaza Suite 2734
George Town,Grand Cayman
Cayman Islands,KY1-4823
EMAIL: m.depree@drvventuresinc.example
web site drvventuresinc.example

COMPANY: skype info drv.ventures.example

second card
Yvette Brannock-Depree
CFO
CELL# 1 555 607 3941
George Town,Grand Cayman
Cayman Islands,KY1-4823
EMAIL: y.brannockdepree@drvventuresinc.example
website drvventuresinc.example

Requirements
Must have
• Business cards must display BOTH logos - DRV is the company and TORVAN is the brand.

```html
<!DOCTYPE html>
<html lang="en">
<head>
<meta charset="utf-8">
<title>DRV Ventures Inc. – Business Card</title>
<link rel="stylesheet" href="https://fonts.googleapis.com/css2?family=Source+Sans+3:wght@400;600;700&display=swap">
<style>
  :root {
    --backdrop: #e4e0d9;
    --card: #ffffff;
    --brand-red: #8e1a1f;
    --ink: #1a1a1a;
    --grey-text: #6e6e6e;
    --band-black: #1c1c1c;
  }
  * { box-sizing: border-box; margin: 0; padding: 0; }
  html, body { width: 1200px; height: 950px; overflow: hidden; }
  body {
    background: var(--backdrop);
    font-family: "Source Sans 3", Arial, sans-serif;
    position: relative;
  }
  .card {
    position: absolute;
    width: 700px;
    height: 400px;
    background: var(--card);
    box-shadow: 0 6px 18px rgba(0,0,0,0.18);
    overflow: hidden;
  }
  .card--front { left: 250px; top: 50px; }
  .card--back  { left: 250px; top: 500px; }

  /* front side */
  .brand-mark {
    position: absolute;
    left: 70px; top: 120px;
    display: flex; align-items: center; gap: 14px;
  }
  .brand-mark__circle {
    width: 70px; height: 70px; border-radius: 50%;
    background: #4a4a4a;
  }
  .brand-mark__name {
    font-weight: 700; font-size: 30px; color: #3c3c3c; line-height: 1.05;
  }
  .company-mark {
    position: absolute;
    display: flex; align-items: center; gap: 12px;
  }
  .card--front .company-mark { left: 380px; top: 128px; }
  .company-mark__square {
    width: 56px; height: 56px; background: var(--brand-red);
  }
  .company-mark__name {
    font-weight: 700; font-size: 30px; color: var(--ink); line-height: 1.05;
  }
  .front-web {
    position: absolute; left: 0; right: 0; bottom: 64px;
    text-align: center; color: var(--grey-text);
    font-size: 17px; letter-spacing: 3px;
  }

  /* back side */
  .card--back .company-mark { left: 50px; top: 50px; }
  .person {
    position: absolute; right: 60px; top: 70px; text-align: right;
  }
  .person__name { color: var(--brand-red); font-size: 26px; font-weight: 400; }
  .person__title { color: var(--ink); font-size: 16px; font-weight: 600; }
  .address {
    position: absolute; left: 50px; top: 190px;
    color: var(--grey-text); font-size: 16px; line-height: 1.3;
  }
  .contacts {
    position: absolute; left: 50px; top: 282px;
    list-style: none; color: var(--grey-text); font-size: 16px; line-height: 1.35;
  }
  .contacts li { display: flex; align-items: center; gap: 8px; }
  .contacts svg { width: 14px; height: 14px; fill: var(--brand-red); flex: none; }
  .band { position: absolute; left: 0; bottom: 0; width: 700px; height: 50px; }
</style>
</head>
<body>

<section class="card card--front" aria-label="Business card front">
  <div class="brand-mark">
    <span class="brand-mark__circle"></span>
    <span class="brand-mark__name">TORVAN<br>SUPPLIES</span>
  </div>
  <div class="company-mark">
    <span class="company-mark__square"></span>
    <span class="company-mark__name">DRV<br>Ventures Inc.</span>
  </div>
  <p class="front-web">www.drvventuresinc.example</p>
</section>

<section class="card card--back" aria-label="Business card back">
  <div class="company-mark">
    <span class="company-mark__square"></span>
    <span class="company-mark__name">DRV<br>Ventures Inc.</span>
  </div>
  <div class="person">
    <p class="person__name">Marisol Depree</p>
    <p class="person__title">CEO</p>
  </div>
  <address class="address" style="font-style:normal">
    Ground floor<br>
    Lindell Plaza Suite 2734<br>
    George Town,Grand Cayman<br>
    Cayman Islands,KY1-4823
  </address>
  <ul class="contacts">
    <li><svg viewBox="0 0 14 14"><rect x="3" y="0" width="8" height="14" rx="1.5"/><rect x="4.5" y="2" width="5" height="8" fill="#fff"/></svg>1 555 4180736</li>
    <li><svg viewBox="0 0 14 14"><rect x="0" y="2" width="14" height="10"/><path d="M0 2 L7 8 L14 2" stroke="#fff" stroke-width="1.4" fill="none"/></svg>m.depree@drvventuresinc.example</li>
    <li><svg viewBox="0 0 14 14"><circle cx="7" cy="7" r="7"/><path d="M1 7 H13 M7 1 C4 4 4 10 7 13 C10 10 10 4 7 1" stroke="#fff" stroke-width="1" fill="none"/></svg>drvventuresinc.example</li>
  </ul>
  <svg class="band" viewBox="0 0 700 50" preserveAspectRatio="none" aria-hidden="true">
    <polygon points="0,40 560,22 560,50 0,50" fill="var(--brand-red)"/>
    <polygon points="566,22 700,4 700,50 566,50" fill="var(--band-black)"/>
  </svg>
</section>

</body>
</html>
```